Website design for legal tech start up in Switzerland (B2B)

We are for a legal tech start up in Switzerland called KOVA. We have been running since August 2016. This will be our first live website.

We need a website designed and business card design for our start-up in Switzerland. We also need the Web design to be converted into HTML and CSS files.

Function of website:
• To inform potential customers of our services
• Form a key part of our digital marketing and sales footprint.
• Branding

Please find attached logo.
Updates

Project Deadline Extended Reason: Giving us time to review submissions and provide opportunity for more submissions. Added Thursday, February 16, 2017

Project Deadline Extended
Reason: Looking for more idea's not necessarily set on blue and grey colours only.

Target Market(s)

B2B tech powered legal services.

Industry/Entity Type

Legal

Contact Information for Business Card

Lean and slick design.

Coding

Coded - Design and coding required

Number of Pages Required

5+ page

Requirements
Must have
• VERY LEAN AND CLEAN DESIGN!
• We have received many great standard designs, but we are looking for something more out-of-the box: You can get inspiration from these designs: http://www.pixelvane.com/websites/clean/
• Thanks!!
• Easy content management system
• Well structured coding for additional development
• Responsive webpage for all types of devices
• SEO optimized
• Tabs (Home, services, team, careers, blog, contact us)
• Colour scheme complementary to logo
Nice to have
• Look and Design - Approachable, High-tech, Modern
• Easy to add chat bot capability in future
Should not have
• Too busy/ too much clutter
• Not take to long to load

```html
<!DOCTYPE html>
<html lang="en">
<head>
<meta charset="utf-8">
<title>KOVA – Agile Legal For Technology Companies</title>
<link href="https://fonts.googleapis.com/css2?family=Tinos:ital,wght@0,400;0,700;1,400&family=Arimo:ital,wght@0,400;0,700;1,400&display=swap" rel="stylesheet">
<style>
:root{
  --navy:#1d4477;
  --navy-dark:#142f55;
  --navy-light:#2c5c97;
  --ink:#333333;
  --grey-text:#555555;
  --grey-soft:#e6e6e6;
  --hex-rim:#d9d9d9;
  --white:#ffffff;
  --footer-bar:#3d3d3d;
}
*{margin:0;padding:0;box-sizing:border-box}
html,body{width:1200px;height:2510px;overflow:hidden;background:var(--white)}
body{position:relative;font-family:"Tinos",serif;color:var(--ink)}
.abs{position:absolute}

/* header */
.top-contact{left:728px;top:0;width:472px;height:34px;background:var(--grey-soft);border-bottom-left-radius:18px;display:flex;align-items:center;padding-left:26px;gap:10px;font-family:"Arimo",sans-serif;font-size:13px;color:var(--ink)}
.round-icon{width:24px;height:24px;border-radius:50%;background:var(--navy);display:inline-block}
.top-contact .socials{display:flex;gap:6px;margin-left:10px}
.brand{left:160px;top:24px;font-family:"Arimo",sans-serif;font-weight:700;font-size:64px;letter-spacing:4px;color:#3a3a3a;line-height:1}
.cta{left:795px;top:55px;width:235px;height:40px;background:var(--navy);color:var(--white);font-size:14px;display:flex;align-items:center;justify-content:center;border-radius:2px;letter-spacing:.3px}

.main-nav{left:0;top:104px;width:1200px;height:43px;background:linear-gradient(#2d5d98,#163a68);display:flex;align-items:center;font-size:14px;color:var(--white)}
.main-nav span{position:absolute;top:13px}
.nav-socials{position:absolute;left:900px;top:8px;display:flex;gap:6px}
.nav-socials i{width:27px;height:27px;border-radius:50%;border:2px solid #c8d2e0;background:#3b4a5e;display:block}

.hero{left:0;top:147px;width:1200px;height:503px;background:linear-gradient(110deg,#2a2f36 0%,#6f8a9e 25%,#c7dde8 45%,#9fb8c8 65%,#425768 100%)}
.hero-title{right:162px;top:243px;text-align:right;font-family:"Arimo",sans-serif;font-weight:700;font-size:32px;line-height:40px;color:var(--white);text-shadow:2px 2px 4px rgba(0,0,0,.6)}
.slide-arrow{top:230px;width:34px;height:26px;background:#2b2b2b;display:flex;align-items:center;justify-content:center}

/* welcome */
.section-title{left:0;width:1200px;text-align:center;font-size:33px;color:#1e1e1e}
.title-rule{width:278px;height:1px;background:#bbbbbb;left:461px}
.title-rule::after{content:"";position:absolute;left:122px;top:-1px;width:34px;height:3px;background:var(--navy)}
.welcome-text{left:179px;top:758px;width:842px;text-align:center;font-size:11.5px;line-height:20px;color:var(--grey-text)}

/* why choose us */
.why{left:0;top:1398px;width:1200px;height:435px;background:linear-gradient(#1f4a80,#102c52);overflow:hidden}
.why .section-title{color:var(--white);font-size:27px;top:42px}
.why .title-rule{top:85px;background:#7d95b7}
.why .title-rule::after{background:var(--white)}
.reason{color:var(--white)}
.reason h3{font-weight:400;font-size:15px;line-height:19px}
.reason p{font-size:11.5px;line-height:18px}
.reason.left{text-align:right}
.why-brand{left:0;top:356px;width:1200px;text-align:center;font-family:"Arimo",sans-serif;font-weight:700;font-size:64px;letter-spacing:4px;color:#3a3a3a;line-height:1}

/* testimonials */
.testimonials .section-title span{color:var(--navy)}
.quote{left:243px;top:1980px;width:761px;text-align:center;font-family:"Arimo",sans-serif;font-style:italic;font-size:14px;line-height:23px;color:var(--ink)}
.quote-mark{font-size:52px;color:#bbbbbb;font-family:"Tinos",serif;line-height:1}
.client-name{left:0;width:1200px;top:2068px;text-align:center;font-family:"Arimo",sans-serif;font-size:14px;color:var(--navy)}
.client-place{left:0;width:1200px;top:2089px;text-align:center;font-family:"Arimo",sans-serif;font-size:13px;color:var(--ink)}
.dots{left:573px;top:2134px;display:flex;gap:9px}
.dots i{width:8px;height:8px;border-radius:50%;background:#999;display:block}
.dots i:first-child{background:var(--navy)}

/* footer */
.site-footer{left:0;top:2184px;width:1200px;height:280px;background:linear-gradient(#234f87,#173a67);color:var(--white)}
.site-footer h4{position:absolute;font-weight:400;font-size:17px}
.quick-links{left:164px;top:82px;list-style:none;font-size:12px;line-height:22px}
.quick-links li::before{content:"› ";}
.contact-line{font-size:12px;line-height:16px;display:flex;gap:8px;align-items:flex-start}
.pin-dot{width:18px;height:18px;border-radius:50%;background:var(--white);flex:none}
.field{left:564px;width:207px;background:var(--white);border:1px solid #cfd7e2;color:var(--ink);font-family:"Arimo",sans-serif;font-size:11px;padding:6px 8px}
.submit{left:564px;top:230px;width:102px;height:31px;background:#111a26;color:var(--white);font-size:14px;display:flex;align-items:center;justify-content:center;gap:10px}
.foot-socials{left:922px;top:97px;display:flex;gap:5px}
.foot-socials i{width:26px;height:26px;border-radius:50%;background:var(--white);display:block}
.foot-brand{left:917px;top:160px;font-family:"Arimo",sans-serif;font-weight:700;font-size:38px;letter-spacing:3px;color:#e3ebf5;line-height:1}
.v-rule{top:44px;width:1px;height:180px;background:#4d73a5}
.copyright{left:0;top:2464px;width:1200px;height:46px;background:var(--footer-bar);color:#dddddd;font-size:12px;display:flex;align-items:center;justify-content:center}
</style>
</head>
<body>

<header>
  <div class="abs top-contact">
    <span class="round-icon"></span>
    <span>Call : 123-456-7890</span>
    <span class="socials"><i class="round-icon"></i><i class="round-icon"></i><i class="round-icon"></i><i class="round-icon"></i></span>
  </div>
  <div class="abs brand">KOVA</div>
  <div class="abs cta">GET A FREE CONSULTATION</div>
</header>

<nav class="abs main-nav">
  <span style="left:186px">Home</span>
  <span style="left:273px">Services</span>
  <span style="left:374px">Team</span>
  <span style="left:457px">Careers</span>
  <span style="left:553px">Blog</span>
  <span style="left:632px">Contact Us</span>
  <span style="left:786px">Follow Us On</span>
  <div class="nav-socials"><i></i><i></i><i></i><i></i></div>
</nav>

<section>
  <div class="abs hero" role="img" aria-label="Business people talking in a bright office, laptop and documents on a desk in the foreground"></div>
  <h1 class="abs hero-title" style="font-weight:700">Agile Legal For Technology<br>Companies</h1>
  <div class="abs slide-arrow" style="left:0;top:377px;width:34px"><svg width="10" height="14"><path d="M8 1 L2 7 L8 13" stroke="#fff" stroke-width="2.5" fill="none"/></svg></div>
  <div class="abs slide-arrow" style="left:1166px;top:377px"><svg width="10" height="14"><path d="M2 1 L8 7 L2 13" stroke="#fff" stroke-width="2.5" fill="none"/></svg></div>
</section>

<section class="welcome">
  <h2 class="abs section-title" style="top:680px;font-weight:400">Welcome to KOVA</h2>
  <div class="abs title-rule" style="top:735px"></div>
  <p class="abs welcome-text">Lorem ipsum dolor sit amet, consectetuer adipiscing elit, sed diam nonummy nibh euismod tincidunt ut laoreet dolore magna aliquam erat volutpat. Ut wisi enim ad minim veniam, quis nostrud exerci tation ullamcorper suscipit lobortis nisl ut aliquip ex ea commodo consequat. Duis autem vel eum iriure dolor in hendrerit in vulputate velit esse molestie consequat, vel illum dolore eu feugiat nulla facilisis at vero eros et accumsan et iusto odio dignissim qui blandit praesent luptatum zzril delenit augue duis dolore. Ut wisi enim ad minim veniam, quis nostrud exerci tation ullamcorper suscipit lobortis nisl ut aliquip ex ea commodo consequat. Duis autem vel eum iriure dolor in hendrerit in vulputate velit esse molestie consequat, vel illum dolore eu feugiat nulla facilisi.</p>
</section>

<section class="services">
  <svg class="abs" style="left:0;top:905px" width="1200" height="450" viewBox="0 905 1200 450">
    <defs>
      <polygon id="hex-rim" points="0,-120 104,-60 104,60 0,120 -104,60 -104,-60"/>
      <polygon id="hex-face" points="0,-108 93,-54 93,54 0,108 -93,54 -93,-54"/>
      <linearGradient id="g-info" x1="0" y1="0" x2="1" y2="1"><stop offset="0" stop-color="#e9eef3"/><stop offset="1" stop-color="#8aa3bd"/></linearGradient>
      <linearGradient id="g-case" x1="0" y1="0" x2="1" y2="1"><stop offset="0" stop-color="#c7d8e8"/><stop offset="1" stop-color="#3e5f86"/></linearGradient>
      <linearGradient id="g-app" x1="0" y1="0" x2="1" y2="1"><stop offset="0" stop-color="#2a3c5c"/><stop offset="1" stop-color="#0f1a2c"/></linearGradient>
      <linearGradient id="g-env" x1="0" y1="0" x2="0" y2="1"><stop offset="0" stop-color="#c9e3a6"/><stop offset="1" stop-color="#3d6a2a"/></linearGradient>
      <linearGradient id="g-word" x1="0" y1="0" x2="1" y2="1"><stop offset="0" stop-color="#3a2a22"/><stop offset="1" stop-color="#b79a82"/></linearGradient>
      <linearGradient id="g-proc" x1="0" y1="0" x2="1" y2="1"><stop offset="0" stop-color="#e2e2e2"/><stop offset="1" stop-color="#6f7176"/></linearGradient>
    </defs>
    <g font-family="Tinos, serif" font-weight="700" font-size="15" fill="#fff" text-anchor="middle">
      <g transform="translate(377,1030)"><use href="#hex-rim" fill="var(--hex-rim)"/><use href="#hex-face" fill="url(#g-info)" role="img" aria-label="Charts and a hand holding a pen over financial documents"/><text y="60">Information Management</text></g>
      <g transform="translate(603,1030)"><use href="#hex-rim" fill="var(--hex-rim)"/><use href="#hex-face" fill="var(--navy)"/><text y="-8" font-size="38" font-weight="400">Our</text><text y="35" font-size="38" font-weight="400">Services</text></g>
      <g transform="translate(825,1030)"><use href="#hex-rim" fill="var(--hex-rim)"/><use href="#hex-face" fill="url(#g-case)" role="img" aria-label="Consultant on the phone at a desk"/><text y="60">Case Support</text></g>
      <g transform="translate(263,1230)"><use href="#hex-rim" fill="var(--hex-rim)"/><use href="#hex-face" fill="url(#g-app)" role="img" aria-label="Hand touching glowing app interface icons"/><text y="60">Application Development</text></g>
      <g transform="translate(487,1230)"><use href="#hex-rim" fill="var(--hex-rim)"/><use href="#hex-face" fill="url(#g-env)" role="img" aria-label="Green forest canopy seen from below"/><text y="60">Environmental Litigation</text></g>
      <g transform="translate(711,1230)"><use href="#hex-rim" fill="var(--hex-rim)"/><use href="#hex-face" fill="url(#g-word)" role="img" aria-label="Hands writing on legal papers at a desk"/><text y="60">Legal Word Processing</text></g>
      <g transform="translate(936,1230)"><use href="#hex-rim" fill="var(--hex-rim)"/><use href="#hex-face" fill="url(#g-proc)" role="img" aria-label="Steel ball bearings and machine parts"/><text y="60">Procurement Support</text></g>
    </g>
  </svg>
</section>

<section class="abs why">
  <h2 class="abs section-title" style="font-weight:400">Why Choose Us</h2>
  <div class="abs title-rule"></div>

  <svg class="abs" style="left:0;top:0" width="1200" height="435">
    <g stroke="#ffffff" stroke-width="2" fill="none">
      <line x1="536" y1="206" x2="560" y2="272"/>
      <line x1="665" y1="206" x2="644" y2="272"/>
      <line x1="430" y1="259" x2="484" y2="318"/>
      <line x1="767" y1="259" x2="720" y2="318"/>
      <line x1="377" y1="360" x2="452" y2="381"/>
      <line x1="820" y1="360" x2="753" y2="381"/>
    </g>
    <circle cx="603" cy="435" r="172" fill="#ffffff" stroke="#2f74c4" stroke-width="6"/>
    <g fill="#ffffff" stroke="#1d4477" stroke-width="2">
      <circle cx="560" cy="272" r="6"/><circle cx="644" cy="272" r="6"/>
      <circle cx="484" cy="318" r="6"/><circle cx="720" cy="318" r="6"/>
      <circle cx="452" cy="381" r="6"/><circle cx="753" cy="381" r="6"/>
    </g>
    <g fill="#ffffff">
      <circle cx="536" cy="206" r="35"/><circle cx="665" cy="206" r="35"/>
      <circle cx="430" cy="259" r="35"/><circle cx="767" cy="259" r="35"/>
      <circle cx="377" cy="360" r="35"/><circle cx="820" cy="360" r="35"/>
    </g>
    <g fill="#1d4477">
      <!-- phone -->
      <path d="M524 194 q4 -4 8 0 l3 6 q1 3 -2 5 q3 7 10 10 q2 -3 5 -2 l6 3 q4 4 0 8 q-6 5 -14 0 q-12 -8 -18 -18 q-4 -8 2 -12z"/>
      <!-- person with question -->
      <circle cx="660" cy="200" r="9"/><path d="M645 226 q15 -20 30 0z"/><circle cx="675" cy="192" r="7" fill="none" stroke="#1d4477" stroke-width="2"/>
      <!-- gear -->
      <circle cx="430" cy="259" r="11" fill="none" stroke="#1d4477" stroke-width="7" stroke-dasharray="4 3"/><circle cx="430" cy="259" r="5"/>
      <!-- calendar -->
      <rect x="753" y="246" width="26" height="24" rx="2" fill="none" stroke="#1d4477" stroke-width="3"/><rect x="753" y="246" width="26" height="6"/><circle cx="779" cy="268" r="8" fill="#fff" stroke="#1d4477" stroke-width="2.5"/>
      <!-- bulb -->
      <circle cx="377" cy="355" r="10"/><rect x="372" y="366" width="10" height="7"/>
      <!-- people -->
      <circle cx="812" cy="352" r="7"/><circle cx="828" cy="352" r="7"/><path d="M800 374 q12 -16 24 0z M816 374 q12 -16 24 0z"/>
    </g>
  </svg>
  <div class="abs why-brand">KOVA</div>

  <div class="abs reason left" style="right:721px;top:122px"><h3>Unbiased Recommendations</h3><p>Lorem ipsum dolor sit mork<br>[+]...adipiscing sed diam</p></div>
  <div class="abs reason left" style="right:825px;top:203px"><h3>Unparalleled<br>Service</h3><p>Lorem ipsum dolor sit mork<br>[+]...adipiscing sed diam</p></div>
  <div class="abs reason left" style="right:879px;top:334px"><h3>Superior Advice</h3><p>Lorem ipsum dolor sit mork<br>[+]...adipiscing sed diam</p></div>
  <div class="abs reason" style="left:721px;top:122px"><h3>Expert Guidance</h3><p>Lorem ipsum dolor sit mork<br>adipiscing sed diam...[+]</p></div>
  <div class="abs reason" style="left:825px;top:220px"><h3>Considerable Time<br>For You</h3><p>Lorem ipsum dolor sit mork<br>adipiscing sed diam...[+]</p></div>
  <div class="abs reason" style="left:879px;top:318px"><h3>Deep Legal Industry<br>Relationships</h3><p>Lorem ipsum dolor sit mork<br>adipiscing sed diam...[+]</p></div>
</section>

<section class="testimonials">
  <h2 class="abs section-title" style="top:1900px;font-size:27px;font-weight:400">Clients <span>Testimonials</span></h2>
  <div class="abs title-rule" style="top:1945px;left:470px;width:260px"></div>
  <div class="abs quote-mark" style="left:193px;top:1966px">“</div>
  <p class="abs quote">Lorem ipsum dolor sit amet, consectetuer adipiscing elit, sed diam nonummy nibh euismod tinciduntol ut laoreet dolore magna aliquam erat volutpat. Ut wisi enim ad minim veniam, quis nostrud exercimori mornkle tation ullamcorper suscipit lobortis nisl ut aliquip ex ea commodo consequat.</p>
  <div class="abs quote-mark" style="left:770px;top:2030px">”</div>
  <svg class="abs" style="left:134px;top:1998px" width="26" height="48"><path d="M24 2 L3 24 L24 46" stroke="#c4c4c4" stroke-width="2" fill="none"/></svg>
  <svg class="abs" style="left:1040px;top:1998px" width="26" height="48"><path d="M2 2 L23 24 L2 46" stroke="#c4c4c4" stroke-width="2" fill="none"/></svg>
  <div class="abs client-name">Marla T.</div>
  <div class="abs client-place">Alder Springs, CA</div>
  <div class="abs dots"><i></i><i></i><i></i><i></i></div>
</section>

<footer class="abs site-footer">
  <h4 style="left:164px;top:50px">Quick Links</h4>
  <ul class="abs quick-links">
    <li>Home</li><li>Services</li><li>Team</li><li>Careers</li><li>Blog</li><li>Contact Us</li>
  </ul>
  <div class="abs v-rule" style="left:298px"></div>

  <h4 style="left:316px;top:50px">Contact Details</h4>
  <div class="abs" style="left:316px;top:86px;display:flex;flex-direction:column;gap:14px">
    <div class="contact-line"><span class="pin-dot"></span><span>Kova Technology<br>Street Name City Name<br>State Zipcode</span></div>
    <div class="contact-line"><span class="pin-dot"></span><span>123-456-7890</span></div>
    <div class="contact-line"><span class="pin-dot"></span><span>123-456-7890</span></div>
    <div class="contact-line"><span class="pin-dot"></span><span>inquiry@kovatechnology.com</span></div>
  </div>
  <div class="abs v-rule" style="left:541px"></div>

  <h4 style="left:564px;top:50px">Quick Inquiry</h4>
  <div class="abs field" style="top:88px;height:32px">Name</div>
  <div class="abs field" style="top:124px;height:31px">Email</div>
  <div class="abs field" style="top:159px;height:61px">Message</div>
  <div class="abs submit">Submit <span>→</span></div>

  <h4 style="left:932px;top:56px">Follow Us</h4>
  <div class="abs foot-socials"><i></i><i></i><i></i><i></i></div>
  <div class="abs foot-brand">KOVA</div>
</footer>

<div class="abs copyright">Copyright © 2017 Kova Technology. All Rights Reserved.</div>

</body>
</html>
```